Meridale Accountants needs a stationery design

We need a stationery design for our new innovative accountancy practise - it is to look professional and reliable but also minimalist, crisp, innovative and fresh. Avoid the use of block colour. You must include letterhead.

We look after business clients and help them get started and grow to successful companies. We provide a range of software, accounting, taxation and business consulting services to these clients.

This is a spin off from our more traditional existing practise - we would like to use the same green and blue.

The final design should communicate professional expertise coupled with innovative technology and personal care. The font of the type should reflect this - so far we have received standard font only.

We need business cards, letterhead, with comp slips, We need to see the whole set to form a view, not just the businesscard

I have uploaded the colours that we want to use from our existing letterhead, being the green and blue. We need to use the KTR logo - also enclosed - please use the text from the enclosed letterhead, but don't refer to this for design purposes - this was our temporary draft only.

Target Market(s)

Small to medium companies, high wealth investor clients

Industry/Entity Type

Professional Service

Requirements
Must have
• Crisp, simple design but evoking innovation, technology, competence and difference.
• So far the designs are too standard and not showing innovation.

```html
<!DOCTYPE html>
<html lang="en">
<head>
<meta charset="utf-8">
<title>Meridale Accountants – Stationery Set</title>
<link href="https://fonts.googleapis.com/css2?family=Source+Sans+3:wght@400;600&family=Jost:wght@400;500&display=swap" rel="stylesheet">
<style>
  :root{
    --backdrop:#a9a8a8;
    --paper:#f5f4f2;
    --green:#7a9a3a;
    --blue:#2e5a8f;
    --navy:#1f3f6b;
    --ink:#4a4a4a;
    --rule:#8c8c8c;
  }
  *{margin:0;padding:0;box-sizing:border-box}
  html,body{width:1200px;height:770px;overflow:hidden}
  body{background:var(--backdrop);position:relative;font-family:"Source Sans 3",sans-serif;color:var(--ink)}
  .sheet{position:absolute;background:var(--paper);box-shadow:0 3px 10px rgba(0,0,0,.25);overflow:hidden}
  .abs{position:absolute}
  .brand{font-family:"Source Sans 3",sans-serif;font-weight:400;color:var(--blue);white-space:nowrap;line-height:1}
  .tagline{font-family:"Source Sans 3",sans-serif;color:var(--blue);white-space:nowrap;line-height:1}
  .band{position:absolute;left:0;bottom:0;width:100%;height:14px}
  .band-url{position:absolute;bottom:1px;color:#fff;font-family:"Source Sans 3",sans-serif;font-size:8.5px;line-height:12px}

  /* letterhead */
  .letterhead{left:62px;top:33px;width:496px;height:701px}
  .letterhead .brand{left:36px;top:64px;font-size:21px}
  .letterhead .tagline{left:89px;top:88px;font-size:9.5px}
  .salutation{left:35px;top:196px;font-size:13px;color:#555}
  .letter-body{left:35px;top:237px;width:426px;font-size:7.6px;line-height:12px;color:#555;text-align:justify}
  .letter-body p{margin-bottom:12px}
  .signoff{left:35px;top:490px;font-size:7.6px;color:#555}
  .signature{left:48px;top:508px;width:70px;height:26px;background:linear-gradient(90deg,rgba(40,40,60,.25),rgba(40,40,60,.05));border-radius:3px}
  .signer{left:53px;top:545px;font-size:8.5px;line-height:13px;color:#555}
  .lh-contact{left:35px;top:630px;font-size:8px;line-height:12px;color:#555}
  .lh-contact div{display:flex;align-items:center;gap:4px}
  .lh-contact svg{width:8px;height:8px;fill:var(--blue)}
  .lh-address{right:38px;top:633px;font-size:8px;line-height:12px;color:#555;text-align:right}

  /* business card */
  .card{left:768px;top:39px;width:219px;height:125px;box-shadow:0 2px 6px rgba(0,0,0,.3)}
  .card-mark{left:12px;top:16px;display:flex;align-items:center;gap:3px;font-size:8px;font-weight:600;color:var(--navy)}
  .card-mark span.sq{width:7px;height:7px;background:var(--green)}
  .card .brand{right:14px;top:16px;font-size:12.5px}
  .card .tagline{right:40px;top:31px;font-size:6px}
  .card-name{left:12px;top:60px;font-size:9px;font-weight:600;color:var(--navy)}
  .card-role{left:12px;top:71px;font-size:5.5px;color:var(--green)}
  .card-rule{left:12px;top:78px;width:195px;height:1px;background:var(--green)}
  .card-contact{left:12px;top:81px;font-size:5.2px;line-height:8.3px;color:#333}
  .card-contact div{display:flex;align-items:center;gap:3px}
  .card-contact svg{width:5px;height:5px;fill:var(--navy)}
  .card-address{right:14px;top:82px;font-size:5.2px;line-height:8.3px;color:#333;text-align:right}
  .card .band{height:8px}
  .card .band-url{font-size:5px;line-height:7px;bottom:0;right:12px}

  /* compliments slip */
  .compliments{left:587px;top:194px;width:560px;height:254px}
  .compliments .brand{left:31px;top:42px;font-size:19px}
  .compliments .tagline{left:79px;top:63px;font-size:8.5px}
  .comp-title{right:38px;top:48px;font-family:"Jost",sans-serif;font-size:22px;color:var(--navy)}
  .comp-line1{left:29px;top:191px;font-family:"Jost",sans-serif;font-size:8.5px;color:#444;white-space:nowrap}
  .comp-line1 .name{color:var(--blue)}
  .comp-rule{left:29px;top:205px;width:494px;height:1px;background:var(--rule)}
  .comp-line2{left:29px;top:209px;font-family:"Jost",sans-serif;font-size:8.5px;color:#444;white-space:nowrap}

  /* second sheet */
  .address-sheet{left:587px;top:480px;width:560px;height:254px}
  .address-sheet .brand{left:31px;top:26px;font-size:19px}
  .address-sheet .tagline{left:81px;top:47px;font-size:8.5px}
  .sheet-details{left:31px;top:72px;font-family:"Jost",sans-serif;font-size:8px;line-height:10.5px;color:#444}
  .sheet-details .name{color:var(--blue)}
  .sheet-details .gap{margin-top:4px}
</style>
</head>
<body>

<!-- Letterhead -->
<section class="sheet letterhead">
  <div class="abs brand">Meridale Accountants</div>
  <div class="abs tagline">Achieve with Clarity</div>

  <p class="abs salutation">Dear Mr. Carter,</p>

  <div class="abs letter-body">
    <p>Lorem ipsum dolor sit amet, consectetur adipiscing elit. Donec orci purus, luctus vitae dignissim eu, iaculis sed purus. Vivamus faucibus, ipsum nec aliquet viverra, leo mauris condimentum ligula, sit amet sagittis enim ligula quis arcu. Nam egestas tortor id nisi porttitor mattis. In tortor ante, ultricies in suscipit a, tempus non massa. Vivamus et auctor mi. Fusce vel massa nulla. Phasellus nec eros mauris, et scelerisque orci.</p>
    <p>Donec malesuada orci vitae nulla accumsan porta a id massa. Quisque accumsan iaculis magna sit amet fringilla. Maecenas consequat, magna eget tincidunt semper, odio nibh rutrum mi, id feugiat ante nisi eu risus. Vestibulum nunc orci, rhoncus a placerat in, ultricies in mi. Cras mattis varius eros, vel fringilla nisi suscipit eget. Quisque scelerisque sagittis nulla at porttitor.</p>
    <p>Sed id augue vitae urna euismod commodo aliquet a quam. Pellentesque arcu velit, cursus et malesuada ut, consequat et diam. Nullam erat sem, rhoncus id ullamcorper vitae, rhoncus et arcu. In ultricies ultricies nulla, ut rutrum nisi iaculis at. Donec eu magna a metus ornare faucibus. Fusce aliquet faucibus ultricies. Morbi semper, est id tincidunt gravida, sem arcu adipiscing lacus, ac bibendum nulla leo eu purus. Quisque nec diam sed risus consectetur a ccumsan quis quis nibh. Vestibulum id purus lorem.</p>
    <p>It is a long established fact that a reader will be distracted by the readable content of a page when looking at its layout. The point of using Lorem Ipsum is that it has a more-or-less normal distribution of letters, as opposed to using 'Content here, content here', making it look like readable English. Many desktop publishing packages</p>
  </div>

  <p class="abs signoff">Sincerely,</p>
  <div class="abs signature" role="img" aria-label="Handwritten signature"></div>
  <div class="abs signer">Daniel Hart<br>CEO/ Founder</div>

  <div class="abs lh-contact">
    <div><svg viewBox="0 0 10 10"><path d="M2 0.5l2 2-1 1.3c.6 1.3 1.6 2.3 2.9 2.9L7.2 5.7l2 2-1.2 1.6C4.5 9.3.7 5.5.5 1.8z"/></svg>(02) 5550 1842</div>
    <div><svg viewBox="0 0 10 10"><path d="M0 2h10v6H0z M0 2l5 3.5L10 2" /></svg>clients@meridaleaccountants.com.au</div>
    <div style="margin-top:2px">ABN 40 555 210 873</div>
  </div>
  <div class="abs lh-address">P O Box 2208, Ashford Vale NSW 2590<br>Suite 4B, Level 3, 12 Harlow Street<br>Ashford Vale NSW 2590</div>

  <svg class="band" viewBox="0 0 496 14" preserveAspectRatio="none">
    <polygon points="0,1 315,1 311,6 0,6" fill="var(--green)"/>
    <polygon points="0,6 311,6 318,0 496,0 496,14 0,14" fill="var(--blue)"/>
  </svg>
  <div class="band-url" style="right:32px">www.meridaleaccountants.com.au</div>
</section>

<!-- Business card -->
<section class="sheet card">
  <div class="abs card-mark"><span class="sq"></span>KTR</div>
  <div class="abs brand">Meridale Accountants</div>
  <div class="abs tagline">Achieve with Clarity</div>
  <div class="abs card-name">Daniel Hart</div>
  <div class="abs card-role">Accountants</div>
  <div class="abs card-rule"></div>
  <div class="abs card-contact">
    <div><svg viewBox="0 0 10 10"><path d="M2 0.5l2 2-1 1.3c.6 1.3 1.6 2.3 2.9 2.9L7.2 5.7l2 2-1.2 1.6C4.5 9.3.7 5.5.5 1.8z"/></svg>(02) 5550 1842</div>
    <div><svg viewBox="0 0 10 10"><rect x="2.5" y="0" width="5" height="10" rx="1"/></svg>0400 555 318</div>
    <div><svg viewBox="0 0 10 10"><rect x="0" y="2" width="10" height="6"/></svg>clients@meridaleaccountants.com.au</div>
    <div><svg viewBox="0 0 10 10"><circle cx="5" cy="5" r="5"/></svg>www.meridaleaccountants.com.au</div>
  </div>
  <div class="abs card-address">ABN 40 555 210 873<br>P O Box 2208, Ashford Vale NSW 2590<br>Suite 4B, Level 3, 12 Harlow Street<br>Ashford Vale NSW 2590</div>
  <svg class="band" viewBox="0 0 219 8" preserveAspectRatio="none">
    <polygon points="0,1 110,1 108,4 0,4" fill="var(--green)"/>
    <polygon points="0,4 108,4 113,0 219,0 219,8 0,8" fill="var(--blue)"/>
  </svg>
  <div class="band-url">Meridale Accountants is a KTR Practice</div>
</section>

<!-- Compliments slip -->
<section class="sheet compliments">
  <div class="abs brand">Meridale Accountants</div>
  <div class="abs tagline">Achieve with Clarity</div>
  <h1 class="abs comp-title" style="font-weight:400">With Compliments</h1>
  <p class="abs comp-line1"><span class="name">Meridale Accountants</span>, P O Box 2208, Ashford Vale NSW 2590 | Suite 4B, Level 3, 12 Harlow Street, Ashford Vale NSW 2590</p>
  <div class="abs comp-rule"></div>
  <p class="abs comp-line2">(02) 5550 1842 | clients@meridaleaccountants.com.au | ABN 40 555 210 873</p>
  <svg class="band" viewBox="0 0 560 14" preserveAspectRatio="none">
    <polygon points="0,1 381,1 377,6 0,6" fill="var(--green)"/>
    <polygon points="0,6 377,6 384,0 560,0 560,14 0,14" fill="var(--blue)"/>
  </svg>
  <div class="band-url" style="right:32px">www.meridaleaccountants.com.au</div>
</section>

<!-- Address sheet -->
<section class="sheet address-sheet">
  <div class="abs brand">Meridale Accountants</div>
  <div class="abs tagline">Achieve with Clarity</div>
  <div class="abs sheet-details">
    <div class="name">Meridale Accountants</div>
    <div>ABN 40 555 210 873</div>
    <div class="gap">P O Box 2208, Ashford Vale NSW 2590</div>
    <div>Suite 4B, Level 3, 12 Harlow Street</div>
    <div>Ashford Vale NSW 2590</div>
  </div>
  <svg class="band" viewBox="0 0 560 14" preserveAspectRatio="none">
    <polygon points="0,1 381,1 377,6 0,6" fill="var(--green)"/>
    <polygon points="0,6 377,6 384,0 560,0 560,14 0,14" fill="var(--blue)"/>
  </svg>
</section>

</body>
</html>
```